Need a stunning home page for Car rental company

For a client, I need a slick and sumber home page design. It is a small, local car rental company, with a handful of cars available for rent.
Selling points: affordable lease, availability, always clean cars
The design should be:
- flat and modern
- no, or very few animations/sliders
- CTA: booking form for renting a car.
- 3 featured cars with images and facts (see website) with button to read more about the car.
- fullscreen background video can be an option
- main colour: #efba01
The site is under construction here:
http://solvikutleie.hammerlia.no/
Delivery requirements:
I need a layered & well organised PSD file delivered.

```html
<!DOCTYPE html>
<html lang="no">
<head>
<meta charset="utf-8">
<title>Solvik Bilutleie – Hjem</title>
<link href="https://fonts.googleapis.com/css2?family=Open+Sans:wght@400;600&display=swap" rel="stylesheet">
<style>
:root{
  --brand:#efba01;
  --brand-light:#ffd54a;
  --ink:#222;
  --text:#444;
  --line:#cfcfcf;
  --footer:#4d4d4d;
  --footer-text:#f0f0f0;
  --white:#fff;
}
*{box-sizing:border-box;margin:0;padding:0}
html,body{width:838px;height:1200px;overflow:hidden;background:var(--white)}
body{position:relative;font-family:"Open Sans",Arial,sans-serif;color:var(--text)}

.site-header{position:absolute;left:0;top:0;width:838px;height:69px}
.brand-name{position:absolute;left:82px;top:22px;font-size:20px;font-weight:600;letter-spacing:1px;color:#555}
.main-nav{position:absolute;right:94px;top:29px;display:flex;gap:10px;font-size:9px;font-weight:600;color:var(--ink)}

.hero{position:absolute;left:0;top:70px;width:838px;height:290px;
  background:linear-gradient(90deg,#c9b25a 0%,#a9a293 40%,#9a9892 70%,#8a8c8f 100%)}
.play-btn{position:absolute;left:342px;top:195px;width:38px;height:38px}

.booking-form{position:absolute;left:402px;top:126px;width:351px;height:177px;background:var(--white);border:1px solid #e2e2e2}
.form-label{position:absolute;left:20px;font-size:8.5px;font-weight:600;color:var(--ink)}
.field{position:absolute;height:19px;border:1px solid var(--line);font-size:8px;color:#666;line-height:17px;padding-left:7px;background:var(--white)}
.field svg{position:absolute;right:5px;top:5px}
.btn{position:absolute;display:block;text-align:center;font-size:10px;color:#5a4300;border-radius:3px;
  background:linear-gradient(180deg,var(--brand-light),var(--brand));border:1px solid #d9a800}

.welcome h1{position:absolute;left:0;width:838px;top:383px;text-align:center;font-size:18px;font-weight:400;color:var(--ink)}
.welcome p{position:absolute;left:104px;width:630px;top:425px;text-align:center;font-size:8.4px;line-height:15.7px;color:var(--ink)}

.car-card{position:absolute;top:533px;width:206px;height:432px;border:1px solid var(--line)}
.car-photo{position:absolute;left:6px;top:6px;width:194px;height:137px;background:linear-gradient(180deg,#b8b8b6,#7d7d7c)}
.car-title{position:absolute;left:6px;top:150px;font-size:15px;font-weight:400;color:var(--brand)}
.spec{position:absolute;left:10px;width:190px;top:182px;font-size:10.3px;color:#333}
.spec div{display:flex;justify-content:space-between;height:23.6px}
.spec span:last-child{width:50px}

.site-footer{position:absolute;left:0;top:1011px;width:838px;height:189px;background:var(--footer);color:var(--footer-text)}
.footer-brand{position:absolute;left:82px;top:12px;font-size:18px;font-weight:600;letter-spacing:1px;color:#8a8a8a}
.contact{position:absolute;left:82px;font-size:8.5px;display:flex;align-items:center;gap:12px}
.contact svg{width:10px;height:10px;fill:var(--footer-text)}
.footer-heading{position:absolute;top:15px;font-size:15px;font-weight:400}
.social{position:absolute;top:1076px;width:32px;height:32px;border:1px solid #c9a233;border-radius:50%}
.links{position:absolute;left:656px;top:42px;font-size:10.3px;line-height:19.6px;list-style:none}
.copyright{position:absolute;left:0;width:838px;top:172px;text-align:center;font-size:7.5px;color:var(--brand)}
</style>
</head>
<body>

<header class="site-header">
  <div class="brand-name">SOLVIK BILUTLEIE</div>
  <nav class="main-nav">
    <span>HJEM</span><span>BILPARKEN VÅR</span><span>TJENESTER</span><span>KONTAKT OSS</span><span>BLOG</span><span>PAGE TEMPLATES</span><span>ABOUT US</span>
  </nav>
</header>

<section class="hero" role="img" aria-label="Bakgrunnsvideo: gul klassisk sportsbil parkert ved en vei">
  <svg class="play-btn" viewBox="0 0 38 38"><circle cx="19" cy="19" r="19" fill="#111"/><path d="M15 11 L27 19 L15 27Z" fill="#fff"/></svg>
</section>

<form class="booking-form">
  <span class="form-label" style="top:29px">SELECT CAR</span>
  <div class="field" style="left:78px;top:24px;width:93px"><svg width="7" height="5"><path d="M0 0H7L3.5 5Z" fill="#666"/></svg></div>

  <span class="form-label" style="top:66px">PICK UP</span>
  <div class="field" style="left:78px;top:61px;width:93px">mm/dd/yyyy<svg width="9" height="9"><rect x=".5" y=".5" width="8" height="8" fill="none" stroke="#3a6ea8"/><rect x="2" y="3" width="5" height="4" fill="#3a6ea8"/></svg></div>
  <div class="field" style="left:183px;top:61px;width:42px">12:00<svg width="6" height="4"><path d="M0 0H6L3 4Z" fill="#666"/></svg></div>
  <div class="field" style="left:236px;top:61px;width:93px">Select Location<svg width="7" height="5"><path d="M0 0H7L3.5 5Z" fill="#666"/></svg></div>

  <span class="form-label" style="top:102px">RETURN</span>
  <div class="field" style="left:78px;top:97px;width:93px">mm/dd/yyyy<svg width="9" height="9"><rect x=".5" y=".5" width="8" height="8" fill="none" stroke="#3a6ea8"/><rect x="2" y="3" width="5" height="4" fill="#3a6ea8"/></svg></div>
  <div class="field" style="left:183px;top:97px;width:42px">12:00<svg width="6" height="4"><path d="M0 0H6L3 4Z" fill="#666"/></svg></div>
  <div class="field" style="left:236px;top:97px;width:93px">Select Location<svg width="7" height="5"><path d="M0 0H7L3.5 5Z" fill="#666"/></svg></div>

  <span class="btn" style="left:21px;top:131px;width:84px;height:26px;line-height:24px">Get A Quote</span>
</form>

<section class="welcome">
  <h1>WELCOME</h1>
  <p>Proin gravida nibh vel velit auctor aliquet. Aenean sollicitudin, lorem quis bibendum auctor, nisi elit consequat ipsum, nec sagittis sem nibh id elit. Duis sed odio sit amet nibh vulputate cursus a sit amet mauris. Morbi accumsan ipsum velit. Nam nec tellus a odio tincidunt auctor a ornare odio. Sed non mauris vitae erat consequat auctor eu in elit. Class aptent taciti sociosqu ad litora torquent per conubia nostra, per inceptos himenaeos. Mauris in erat justo. Nullam ac urna eu felis dapibus condimentum sit amet a augue. Sed non neque elit. Sed ut imperdiet nisi.</p>
</section>

<article class="car-card" style="left:82px">
  <div class="car-photo" role="img" aria-label="Foto: hvit varebil"></div>
  <h2 class="car-title">Varebilen</h2>
  <div class="spec">
    <div><span>Pris per døgn</span><span>kr 600</span></div>
    <div><span>BiltypeVarebil</span><span>Varebil</span></div>
    <div><span>Maks. pers.</span><span>2</span></div>
    <div><span>Ant. dører</span><span>5</span></div>
    <div><span>Min. sjåføralder</span><span>21</span></div>
    <div><span>Girtype?</span><span>Manuell</span></div>
    <div><span>Klimaanlegg?</span><span>Ja</span></div>
    <div><span>Ubegrenset km?</span><span>Nei</span></div>
  </div>
  <span class="btn" style="left:55px;top:380px;width:83px;height:26px;line-height:24px">Read More</span>
</article>

<article class="car-card" style="left:317px">
  <div class="car-photo" role="img" aria-label="Foto: rød sedan"></div>
  <h2 class="car-title">Varebilen</h2>
  <div class="spec">
    <div><span>Pris per døgn</span><span>kr 600</span></div>
    <div><span>BiltypeVarebil</span><span>Varebil</span></div>
    <div><span>Maks. pers.</span><span>2</span></div>
    <div><span>Ant. dører</span><span>5</span></div>
    <div><span>Min. sjåføralder</span><span>21</span></div>
    <div><span>Girtype?</span><span>Manuell</span></div>
    <div><span>Klimaanlegg?</span><span>Ja</span></div>
    <div><span>Ubegrenset km?</span><span>Nei</span></div>
  </div>
  <span class="btn" style="left:55px;top:380px;width:83px;height:26px;line-height:24px">Read More</span>
</article>

<article class="car-card" style="left:548px">
  <div class="car-photo" role="img" aria-label="Foto: sølvfarget sedan"></div>
  <h2 class="car-title">Varebilen</h2>
  <div class="spec">
    <div><span>Pris per døgn</span><span>kr 600</span></div>
    <div><span>BiltypeVarebil</span><span>Varebil</span></div>
    <div><span>Maks. pers.</span><span>2</span></div>
    <div><span>Ant. dører</span><span>5</span></div>
    <div><span>Min. sjåføralder</span><span>21</span></div>
    <div><span>Girtype?</span><span>Manuell</span></div>
    <div><span>Klimaanlegg?</span><span>Ja</span></div>
    <div><span>Ubegrenset km?</span><span>Nei</span></div>
  </div>
  <span class="btn" style="left:55px;top:380px;width:83px;height:26px;line-height:24px">Read More</span>
</article>

<footer class="site-footer">
  <div class="footer-brand">SOLVIK BILUTLEIE</div>

  <div class="contact" style="top:52px"><svg viewBox="0 0 10 10"><path d="M5 0L10 5H8.5V10H6V7H4V10H1.5V5H0Z"/></svg>Solvik Bilutleie</div>
  <div class="contact" style="top:84px"><svg viewBox="0 0 10 10"><path d="M0 2H10V8H0Z M0 2L5 6L10 2" fill="none" stroke="#f0f0f0"/></svg>Email: info@solvikutleie.no, hjelp@solvikutleie.no</div>
  <div class="contact" style="top:115px"><svg viewBox="0 0 10 10"><path d="M0 3Q5 0 10 3V5H7.5V4H2.5V5H0Z M2 6H8L9 9H1Z"/></svg>Phone: (555) 214-7730</div>
  <div class="contact" style="top:146px"><svg viewBox="0 0 10 10"><rect x="2.5" y="0" width="5" height="10" rx="1"/></svg>Mobile phone: 47 21 86 30</div>

  <h3 class="footer-heading" style="left:381px">Follow us</h3>

  <h3 class="footer-heading" style="left:655px">Main Links</h3>
  <ul class="links">
    <li>Home</li><li>About</li><li>Folio</li><li>Services</li><li>Blog</li><li>Contact</li>
  </ul>

  <p class="copyright">© Solvik Bilutleie 2014. All rights reserved.</p>
</footer>

<span class="social" style="left:383px" aria-label="Sosialt nettverk 1"></span>
<span class="social" style="left:424px" aria-label="Sosialt nettverk 2"></span>
<span class="social" style="left:465px" aria-label="Sosialt nettverk 3"></span>

</body>
</html>
```